Local massage therapist needs some new marketing material

Hi there! I am a massage therapist here in Denver, CO in Alder Bend(shopping and art district) of the city. My business is called Lumo Bodywork of Denver. My practice has an eastern influence and I do reflexology, thai massage and use Chinese herbs, etc. I know all my clients and pay close attention to details. I am also very respectful of tradition and it shows in how I work. I tend to like modern, clean, fun, Asian designs. I am wanting a new business card and brochure. I have a logo and branding for my business that I want used in the design. Currently, the sign for my building is purple and I think my logo was designed to be purple. I will attach pictures of it and can send whatever files are necessary so it can be integrated into the brochure, etc. I like the purple but open to using other colors as well. Thanks!
My website is lumobodyworkofdenver.example where info can be gathered about me and services/fees for brochure.
Updates

Just increased budget. Please see new feedback in discussion thread.

Thanks!

                                       HEY ALL,

Just wanted to let you know that I made a change to my website. It is on the Prices Page. I no longer have the frequent  flyer prices but I added discounts. Let me know if you have any questions. Thanks so much!

Target Market(s)

healthy, urban, educated, upper middle class, yogis

Industry/Entity Type

Marketing

Requirements
Must have
• logo stays purple
Should not have
• not too busy

```html
<!DOCTYPE html>
<html lang="en">
<head>
<meta charset="utf-8">
<title>Lumo Bodywork of Denver – Business Card</title>
<link rel="stylesheet" href="https://fonts.googleapis.com/css2?family=Open+Sans:ital,wght@0,400;0,600;0,700;1,400&display=swap">
<style>
  :root {
    --purple: #5e2a91;
    --charcoal: #333335;
    --ink: #4a4a4a;
    --rule: #9a9a9a;
    --paper: #ffffff;
    --backdrop: #ecebe8;
  }
  * { box-sizing: border-box; margin: 0; padding: 0; }
  html, body { width: 1200px; height: 720px; overflow: hidden; }
  body {
    background: var(--backdrop);
    font-family: "Open Sans", Arial, sans-serif;
    color: var(--ink);
    display: flex;
    align-items: center;
    justify-content: center;
    gap: 40px;
  }
  .card {
    position: relative;
    width: 540px;
    height: 308px;
    background: var(--paper);
    box-shadow: 0 2px 10px rgba(0,0,0,.12);
    overflow: hidden;
  }
  .card-front__bands { position: absolute; inset: 0; }
  .holder {
    position: absolute; right: 26px; top: 10px;
    color: var(--paper); text-align: right; line-height: 1.15;
  }
  .holder__name { font-size: 17px; font-weight: 700; }
  .holder__title { font-size: 11px; }

  .brand { display: flex; align-items: center; gap: 12px; color: var(--purple); }
  .brand__dot { width: 16px; height: 16px; border-radius: 50%; background: var(--purple); }
  .brand__name { font-size: 58px; font-weight: 400; letter-spacing: 8px; line-height: 1; }

  .card-front .brand { position: absolute; left: 34px; top: 150px; }

  .contact {
    position: absolute; left: 34px; top: 232px;
    list-style: none; font-size: 12.5px; line-height: 20px;
  }
  .contact li { display: flex; align-items: center; gap: 6px; }
  .contact svg { width: 12px; height: 12px; flex: none; }

  .address {
    position: absolute; left: 330px; top: 228px;
    border-left: 1px solid var(--rule);
    padding-left: 12px; font-size: 12.5px; line-height: 20px;
  }

  .card-back .brand { position: absolute; right: 30px; top: 40px; }
  .card-back .brand__name { font-size: 46px; letter-spacing: 6px; }

  .appointment { position: absolute; left: 34px; top: 118px; right: 30px; }
  .appointment__heading {
    color: var(--purple); font-size: 14px; font-weight: 700; letter-spacing: .3px;
    margin-bottom: 18px;
  }
  .field-row { display: flex; align-items: flex-end; font-size: 14px; margin-bottom: 10px; }
  .field-line { display: inline-block; border-bottom: 1px solid var(--rule); height: 14px; margin: 0 6px; }
  .hours { font-size: 14.5px; line-height: 21px; margin-top: 12px; }
  .notice { font-size: 14px; font-style: italic; color: #6b6b6b; margin-top: 12px; }
</style>
</head>
<body>

  <section class="card card-front" aria-label="Business card front">
    <svg class="card-front__bands" viewBox="0 0 540 308" preserveAspectRatio="none" aria-hidden="true">
      <polygon points="190,0 540,0 540,46 262,56" fill="var(--purple)"/>
      <path d="M262,56 L540,46 L540,52 C505,56 492,78 490,96 Z" fill="var(--charcoal)"/>
    </svg>
    <div class="holder">
      <div class="holder__name">Your Name</div>
      <div class="holder__title">Title</div>
    </div>

    <div class="brand">
      <span class="brand__dot"></span>
      <span class="brand__name">LUMO</span>
    </div>

    <ul class="contact">
      <li>
        <svg viewBox="0 0 12 12" aria-hidden="true"><circle cx="6" cy="6" r="6" fill="var(--purple)"/><path d="M4 3.2l1 .1.5 1.4-.7.6a4 4 0 0 0 1.9 1.9l.6-.7 1.4.5.1 1c-3 .6-5.4-1.8-4.8-4.8z" fill="#fff"/></svg>
        303.555.0142
      </li>
      <li>
        <svg viewBox="0 0 12 12" aria-hidden="true"><circle cx="6" cy="6" r="6" fill="var(--purple)"/><rect x="3" y="4" width="6" height="4.2" fill="#fff"/><path d="M3 4l3 2.4L9 4" stroke="var(--purple)" stroke-width=".8" fill="none"/></svg>
        info@lumobodyworkofdenver.example
      </li>
      <li>
        <svg viewBox="0 0 12 12" aria-hidden="true"><circle cx="6" cy="6" r="6" fill="var(--purple)"/><circle cx="6" cy="6" r="3.3" stroke="#fff" stroke-width=".8" fill="none"/><path d="M2.7 6h6.6M6 2.7c-1.8 2-1.8 4.6 0 6.6M6 2.7c1.8 2 1.8 4.6 0 6.6" stroke="#fff" stroke-width=".6" fill="none"/></svg>
        www.lumobodyworkofdenver.example
      </li>
    </ul>

    <div class="address">
      1480 E Larkspur Ave<br>
      Denver, CO 80206
    </div>
  </section>

  <section class="card card-back" aria-label="Business card back, appointment reminder">
    <div class="brand">
      <span class="brand__dot"></span>
      <span class="brand__name">LUMO</span>
    </div>

    <div class="appointment">
      <h2 class="appointment__heading">YOUR APPOINTMENT</h2>
      <div class="field-row">
        Name :<span class="field-line" style="width:120px"></span>
        Time :<span class="field-line" style="width:110px"></span>am / pm
      </div>
      <div class="field-row">
        Date :<span class="field-line" style="width:120px"></span>
      </div>
      <p class="hours">
        Tues - Fri 10am - 8pm Sat 10am-5pm<br>
        (Appointments required) No walk-ins please.
      </p>
      <p class="notice">We appreciate a 24 hr. notice for cancellations</p>
    </div>
  </section>

</body>
</html>
```